Counseling Practice Business Card

I need a professional looking business card incorporating my new logo that was just completed. Card needs to incorporate my name and title, description of my specialty, my address, my phone number, my fax number, my email and my website URL. I need to be able to choose design on/with different paper colors and textures.
I do not have a lot of business card ideas so I am open to anything but I want bold,sharp, clear card without additional designs other than my logo (see attached file info). I am open to different color backgrounds or paper colors including black. I do not like traditional brackets around area codes in phone number or dashes between numbers in phone number. Am open to other ways of presenting including periods between numbers as appropriate. I do not know enough to know what I like yet but I want card to coordinate and work together with my logo. My practice emphasizes natural mental health interventions so any use of color (with background paper color or the blue and green in my logo) that elicits nature is nice. In addition to black, any natural brown or wood looking background might be desirable also. Most of the offerings so far look very similar and boring.

Target Market(s)

Potential therapy clients and other professionals

Contact Information for Business Card

Card information:
Gerald M. Whitcombe, Ph.D.
Licensed Clinical Psychologist
Integrative Health Coach
4812 Marlowe Ridge Blvd SE
Suite 310
Alder Falls, GA 30418
(770) 415-2983 phone
(770) 581-4096 fax
drgeraldwhitcombe@quillmarsh.net
brightfernwellness.net

Font styles to use
Serif
Sans Serif
Other font styles liked:
• anything that you think looks crisp, clear and easily readable

Requirements
Must have
• Any color used should coordinate with my logo design (see attached files).
• Card should be printed horizontally so top and bottom are longest sides of rectangle.
• Background color or paper color should complement and highlight logo. Do not like a white background. black, grey, brown or any color my logo would blend well with.
Nice to have
• I would like designer to utilize color to highlight letters/name or phone-fax-web symbols.
• Bottom edge of card could be highlighted if appropriate to an idea.
Should not have
• I would NOT want the card to have a pure white background at all.
• No clear cards.
• Cards should be oriented with long sides on bottom and top, NOT sides. DO NOT LIKE THIS THIN TALL ORIENTATION.

```html
<!DOCTYPE html>
<html lang="en">
<head>
<meta charset="utf-8">
<title>Brightfern Wellness – Business Card</title>
<link href="https://fonts.googleapis.com/css2?family=Oswald:wght@400;500&display=swap" rel="stylesheet">
<style>
  :root {
    --backdrop: #a7abaa;
    --kraft: #d3ab8f;
    --kraft-edge: #c69d80;
    --ink-brown: #85593a;
    --rule-brown: #6f4a2c;
    --brand-blue: #2f86cf;
  }
  * { box-sizing: border-box; margin: 0; padding: 0; }
  html, body {
    width: 1200px; height: 824px; overflow: hidden;
    background: var(--backdrop);
  }
  .canvas {
    width: 1200px; height: 824px;
    display: flex; align-items: center; justify-content: center; gap: 48px;
  }
  .card {
    position: relative;
    width: 540px; height: 309px;
    background: var(--kraft);
    box-shadow: 0 2px 0 var(--kraft-edge), 0 10px 24px rgba(0,0,0,.18);
  }
  .card-frame {
    position: absolute; inset: 13px;
    border: 2px solid var(--rule-brown);
    outline: 1px solid var(--rule-brown);
    outline-offset: -6px;
  }
  /* contact side */
  .contact-list {
    position: absolute; inset: 30px 42px;
    list-style: none;
    display: flex; flex-direction: column; justify-content: center; gap: 9px;
    font-family: "Oswald", sans-serif;
    color: var(--ink-brown);
  }
  .contact-item { display: flex; align-items: center; gap: 14px; }
  .contact-icon { flex: 0 0 22px; width: 22px; height: 22px; }
  .contact-text { font-size: 14px; line-height: 1.2; letter-spacing: .2px; }
  .contact-name { font-size: 19px; font-weight: 500; }
  /* brand side */
  .brand {
    position: absolute; inset: 0;
    display: flex; align-items: center; justify-content: center; gap: 14px;
    font-family: "Oswald", sans-serif;
    font-weight: 500; font-size: 40px; letter-spacing: 1px;
    color: var(--brand-blue);
  }
  .brand-dot { width: 26px; height: 26px; border-radius: 50%; background: var(--brand-blue); }
</style>
</head>
<body>
<main class="canvas">
  <section class="card card-contact" aria-label="Contact side">
    <div class="card-frame"></div>
    <ul class="contact-list">
      <li class="contact-item">
        <svg class="contact-icon" viewBox="0 0 22 22"><circle cx="11" cy="11" r="10" fill="none" stroke="var(--ink-brown)" stroke-width="1.6"/><circle cx="11" cy="8.5" r="3" fill="var(--ink-brown)"/><path d="M5.5 16.5c1-3 3-4 5.5-4s4.5 1 5.5 4z" fill="var(--ink-brown)"/></svg>
        <div class="contact-text"><div class="contact-name">Gerald M. Whitcombe, Ph.D.</div>Licensed Clinical Psychologist<br>Integrative Health Coach</div>
      </li>
      <li class="contact-item">
        <svg class="contact-icon" viewBox="0 0 22 22"><circle cx="11" cy="11" r="10" fill="none" stroke="var(--ink-brown)" stroke-width="1.6"/><path d="M11 17s-4-4.5-4-7.5a4 4 0 0 1 8 0c0 3-4 7.5-4 7.5z" fill="var(--ink-brown)"/><circle cx="11" cy="9.5" r="1.5" fill="var(--kraft)"/></svg>
        <div class="contact-text">4812 Marlowe Ridge Blvd SE<br>Suite 310, Alder Falls, GA 30418</div>
      </li>
      <li class="contact-item">
        <svg class="contact-icon" viewBox="0 0 22 22"><circle cx="11" cy="11" r="10" fill="none" stroke="var(--ink-brown)" stroke-width="1.6"/><path d="M7.5 6.5l2 0 1 2.5-1.3 1a6 6 0 0 0 2.8 2.8l1-1.3 2.5 1v2c-5 .5-8.5-3-8-8z" fill="var(--ink-brown)"/></svg>
        <div class="contact-text">(770) 415-2983</div>
      </li>
      <li class="contact-item">
        <svg class="contact-icon" viewBox="0 0 22 22"><circle cx="11" cy="11" r="10" fill="none" stroke="var(--ink-brown)" stroke-width="1.6"/><rect x="6" y="8" width="10" height="7" rx="1" fill="var(--ink-brown)"/><rect x="8" y="5.5" width="6" height="3" fill="none" stroke="var(--ink-brown)" stroke-width="1.2"/></svg>
        <div class="contact-text">(770) 581-4096</div>
      </li>
      <li class="contact-item">
        <svg class="contact-icon" viewBox="0 0 22 22"><circle cx="11" cy="11" r="10" fill="none" stroke="var(--ink-brown)" stroke-width="1.6"/><rect x="6" y="7.5" width="10" height="7" fill="var(--ink-brown)"/><path d="M6 7.5l5 4 5-4" fill="none" stroke="var(--kraft)" stroke-width="1.1"/></svg>
        <div class="contact-text">drgeraldwhitcombe@quillmarsh.net</div>
      </li>
      <li class="contact-item">
        <svg class="contact-icon" viewBox="0 0 22 22"><circle cx="11" cy="11" r="10" fill="none" stroke="var(--ink-brown)" stroke-width="1.6"/><circle cx="11" cy="11" r="5" fill="none" stroke="var(--ink-brown)" stroke-width="1.3"/><path d="M6 11h10M11 6c-2 3-2 7 0 10M11 6c2 3 2 7 0 10" fill="none" stroke="var(--ink-brown)" stroke-width="1"/></svg>
        <div class="contact-text">brightfernwellness.net</div>
      </li>
    </ul>
  </section>

  <section class="card card-brand" aria-label="Brand side">
    <div class="card-frame"></div>
    <div class="brand"><span class="brand-dot"></span><span class="brand-name">Brightfern Wellness</span></div>
  </section>
</main>
</body>
</html>
```